BOND WITH JASPER FOR SPECIALISED ADHESIVE AND SEALANTS.

Details for my new Banner Ad Design Project will be added soon.
All that I am looking for is WORDING that can demonstrate to potential customers what the products can achieve and describing the various materials that this special adhesive will stick and why they need to choose it also a logo or even new name to fit in if financially possible
The size of the banner is unimportant as I only need help in getting the message over then I will adjust accordingly or pay the designer to complete.
As I am very limited in my knowledge of web design in fact it is non existent your help is paramount for the result.
This is a new project for me as I am now a young retired person who is looking for something different to follow.
Please let me know if the information I supply is in sufficient,
Best regards to all and in your design careers.
Updates

As pointed out to me that my request is to broad for a result,but I am not looking for words that describe a space shot, I am looking for suggestions to help me to put together some form of ad that helps me get the business off the ground ,I am no expert in marketing and design, so any format of words would be helpful,thank you all and remember, " you are the experts".

Target Market(s)

General public in the UK,and commercial business.
It would be used where there is a requirement to seal/or stick difficult materials or items but not large items like roofs/buildings etc.

Industry/Entity Type

Adhesive

Font styles to use
Sans Serif

Colors

Designer to choose colors to be used in the design.

Requirements
Must have
• To make people feel they will need the product or service maybe not initially but soon.
Nice to have
• This can be anything related to sticking or sealing different household products,
Should not have
• old fashioned font

```html
<!DOCTYPE html>
<html lang="en">
<head>
<meta charset="utf-8">
<title>Bond With Jasper – Special Adhesive Banner</title>
<link href="https://fonts.googleapis.com/css2?family=Montserrat:wght@300;400;500;600&display=swap" rel="stylesheet">
<style>
  :root {
    --page-bg: #232325;
    --brand-orange: #ff8243;
    --brand-red: #b92507;
    --label-blue: #a5d8f7;
    --photo-light: #d3e6f2;
    --photo-mid: #b7d5ea;
    --ink: #2a2f38;
    --white: #ffffff;
  }
  * { margin: 0; padding: 0; box-sizing: border-box; }
  html, body {
    width: 1200px; height: 750px; overflow: hidden;
    background: var(--page-bg);
    font-family: "Montserrat", sans-serif;
  }
  .banner {
    position: absolute; left: 4px; top: 200px;
    width: 1192px; height: 350px;
    background: var(--white);
  }
  .brand-panel {
    position: absolute; left: 0; top: 0;
    width: 537px; height: 270px;
    background: var(--brand-orange);
    color: var(--white);
  }
  .brand-name { position: absolute; left: 66px; top: 12px; font-weight: 300; line-height: 1; }
  .brand-name__first { display: block; font-size: 102px; letter-spacing: 1px; }
  .brand-name__second { display: flex; align-items: baseline; margin-top: -4px; }
  .brand-name__with { font-size: 36px; margin-right: 8px; }
  .brand-name__last { font-size: 82px; letter-spacing: 0; }
  .product-tag {
    position: absolute; right: 66px; top: 207px;
    background: var(--label-blue);
    color: #111;
    font-size: 20px; font-weight: 400; letter-spacing: 1.6px;
    padding: 6px 12px 5px;
  }
  .contact-bar {
    position: absolute; left: 0; top: 270px;
    width: 537px; height: 80px;
    background: var(--brand-red);
    color: var(--white);
    text-align: right;
    padding: 10px 19px 0 0;
    font-size: 19.5px; font-weight: 400; line-height: 31px;
  }
  .product-visual {
    position: absolute; left: 539px; top: 0;
    width: 653px; height: 350px;
    background: linear-gradient(100deg, var(--photo-mid) 0%, var(--photo-light) 60%, #eef4f8 100%);
  }
  .materials {
    position: absolute; left: 578px; top: 30px;
    color: var(--ink);
  }
  .materials__title { font-size: 29px; font-weight: 600; letter-spacing: 2px; margin-bottom: 13px; }
  .materials__list { list-style: none; font-size: 22px; font-weight: 500; letter-spacing: 1.2px; line-height: 30px; }
  .materials__more { font-size: 19px; font-weight: 500; letter-spacing: 0.6px; margin-top: 2px; }
</style>
</head>
<body>
  <div class="banner">
    <section class="brand-panel">
      <h1 class="brand-name">
        <span class="brand-name__first">BOND</span>
        <span class="brand-name__second">
          <span class="brand-name__with">WITH</span>
          <span class="brand-name__last">JASPER</span>
        </span>
      </h1>
      <div class="product-tag">SPECIAL ADHESIVE</div>
    </section>
    <footer class="contact-bar">
      <p>email - hello@bondwithjasper.com</p>
      <p>tel - 144 210 7391</p>
    </footer>
    <div class="product-visual" role="img" aria-label="Photo of a white glue bottle with an orange nozzle and a drop of white glue on a pale blue surface"></div>
    <section class="materials">
      <h2 class="materials__title">STICKS</h2>
      <ul class="materials__list">
        <li>GLASS</li>
        <li>LEATHER</li>
        <li>WOOD</li>
        <li>STEEL</li>
        <li>CARD</li>
        <li>CLOTH</li>
        <li>ALL PLASTICS</li>
      </ul>
      <p class="materials__more">and much much more....</p>
    </section>
  </div>
</body>
</html>
```